Personal loan pre-approval

We are a credit union sending out pre-approvals for personal loans. I am attaching a letter that we sent out during previous pre-approvals. The fine print needs to be included on the postcard from the letter, but the rest is just a guide. The theme I'm thinking of may be Easy, Cold Hard Cash, but I'm not stuck on it. Thanks.

http://www.brightleafprint.com/gallerydetail.aspx?sectionID=143&photoID=104

The cash banner is an example of what I had in mind.

We don't want the actual letter on the postcard, it was meant to be a guide only as to what we are selling. The front page should be explaining that they are pre-approved for a personal loan, say up $10,000, at a rate of 7.99% APR*. It should be mentioned how they are pre-approved, which means no credit check, no proof of income needed. Somewhere, either on the front or the back, needs to be the fine print in a discreet fashion. look at the link I provide for some guidance. Thanks!
Updates

Industry/Entity Type

Union

Requirements
Must have
• Must have fine print on postcard that is on example letter.
Should not have
• Should not have the entire letter on the postcard

```html
<!DOCTYPE html>
<html lang="en">
<head>
<meta charset="utf-8">
<title>Signature Loan Pre-Approval Postcard</title>
<link href="https://fonts.googleapis.com/css2?family=Anton&family=Open+Sans:wght@400;600&family=Cormorant+Garamond:wght@500;600&display=swap" rel="stylesheet">
<style>
  :root {
    --navy: #243a86;
    --navy-deep: #1c2f70;
    --white: #ffffff;
    --ink: #2a2320;
    --desk: #d9c7ab;
    --sleeve: #c58fc3;
    --paper: #f2efe8;
  }
  * { margin: 0; padding: 0; box-sizing: border-box; }
  html, body { width: 1200px; height: 776px; overflow: hidden; background: var(--white); }
  .postcard {
    position: relative;
    width: 1200px;
    height: 776px;
    overflow: hidden;
  }
  .hero-photo {
    position: absolute;
    inset: 0;
    background:
      radial-gradient(ellipse 520px 360px at 880px 90px, rgba(197,143,195,0.95), rgba(197,143,195,0) 70%),
      radial-gradient(ellipse 420px 260px at 1100px 420px, rgba(224,170,150,0.85), rgba(224,170,150,0) 70%),
      radial-gradient(ellipse 520px 180px at 520px 560px, rgba(242,239,232,0.95), rgba(242,239,232,0) 75%),
      radial-gradient(ellipse 420px 260px at 980px 640px, rgba(236,228,205,0.95), rgba(236,228,205,0) 75%),
      radial-gradient(ellipse 380px 320px at 150px 300px, rgba(214,170,150,0.8), rgba(214,170,150,0) 70%),
      linear-gradient(180deg, #f1ece8 0%, #e6d7cf 40%, var(--desk) 75%, #d2bea0 100%);
  }
  .headline {
    position: absolute;
    left: 42px;
    color: var(--white);
    font-family: "Anton", "Arial Narrow", sans-serif;
    text-shadow:
      2px 0 0 var(--navy), -2px 0 0 var(--navy), 0 2px 0 var(--navy), 0 -2px 0 var(--navy),
      2px 2px 0 var(--navy), -2px -2px 0 var(--navy), 2px -2px 0 var(--navy), -2px 2px 0 var(--navy);
    line-height: 1;
  }
  .headline--intro {
    top: 96px;
    font-size: 36px;
    letter-spacing: 0.3px;
    color: var(--navy);
    text-shadow:
      2px 0 0 var(--white), -2px 0 0 var(--white), 0 2px 0 var(--white), 0 -2px 0 var(--white),
      2px 2px 0 var(--white), -2px -2px 0 var(--white), 2px -2px 0 var(--white), -2px 2px 0 var(--white);
  }
  .headline--amount { top: 160px; font-size: 118px; }
  .headline--product { top: 262px; font-size: 118px; letter-spacing: 1px; }
  .loan-terms {
    position: absolute;
    left: 380px;
    top: 406px;
    font-family: "Open Sans", Arial, sans-serif;
    font-size: 21px;
    line-height: 29px;
    color: var(--ink);
  }
  .lender {
    position: absolute;
    right: 48px;
    top: 66px;
    display: flex;
    align-items: center;
    gap: 10px;
  }
  .lender__mark { width: 42px; height: 42px; background: var(--navy); }
  .lender__name {
    font-family: "Open Sans", Arial, sans-serif;
    font-weight: 600;
    font-size: 17px;
    line-height: 20px;
    color: var(--navy);
  }
  .rate-band {
    position: absolute;
    left: 0;
    bottom: 0;
    width: 790px;
    height: 114px;
  }
  .rate-band svg { position: absolute; inset: 0; }
  .rate-band__text {
    position: absolute;
    left: 48px;
    top: 10px;
    display: flex;
    align-items: baseline;
    gap: 30px;
    color: var(--white);
    font-family: "Cormorant Garamond", "Times New Roman", serif;
    font-weight: 600;
  }
  .rate-band__label { font-size: 27px; }
  .rate-band__value { font-size: 84px; letter-spacing: 3px; line-height: 1.1; }
</style>
</head>
<body>
  <main class="postcard">
    <div class="hero-photo" role="img" aria-label="Photo of a woman's hands writing a check with a fountain pen beside a stack of cash on a desk"></div>

    <div class="lender">
      <span class="lender__mark"></span>
      <span class="lender__name">Harbor Valley Teachers<br>Credit Union</span>
    </div>

    <h1>
      <span class="headline headline--intro">You have been pre-approved for:</span>
      <span class="headline headline--amount">$7000</span>
      <span class="headline headline--product">Signature Loan</span>
    </h1>

    <p class="loan-terms">including existing loan balances*<br>Up to 60 month term</p>

    <div class="rate-band">
      <svg width="790" height="114" viewBox="0 0 790 114" aria-hidden="true">
        <polygon points="0,0 706,0 790,114 0,114" fill="var(--navy)"/>
      </svg>
      <p class="rate-band__text">
        <span class="rate-band__label">Rate as low as</span>
        <span class="rate-band__value">9.95% APR</span>
      </p>
    </div>
  </main>
</body>
</html>
```